Mobile Fitness snd Therapy Business Card Design

I need a business card designed for my mobile fitness and therapy business.

Please view the images that I have uploaded. I like the simplicity of the design that I have attached. I adapted it with my information

Target Market(s)

Those seeking personal training, injury rehabilitation or massage therapy.

Industry/Entity Type

Business

Contact Information for Business Card

Derek Fulham - MSc, CAT(C), RMT, CSCS, Pn2
e-mail: derek@vantrelo.com
website: www.vantrelo.com
instagram: @derek_fulham

Font styles to use
Sans Serif

Colors
3176b5
0355a3

Requirements
Must have
• "Contact us to receive a FREE assessment"
• Services offered:
• Personal Training
• Golf Fitness
• Injury Rehab
• Massage Therapy
• Yoga
Nice to have
• Consistent colours with brand
• - Dark Blue: #232837
• - Blue: #5096f0
• Consistent look/feel with the website: www.vantrelo.com

```html
<!DOCTYPE html>
<html lang="en">
<head>
<meta charset="utf-8">
<title>Vantrelo Business Card</title>
<link href="https://fonts.googleapis.com/css2?family=Roboto:wght@400;500;700&display=swap" rel="stylesheet">
<style>
  :root {
    --dark-navy: #232837;
    --brand-blue: #5096f0;
    --accent-blue: #3176b5;
    --text-grey: #5a5d66;
    --rule-grey: #d3d5da;
    --card-white: #fbfbfc;
    --stage: #e9eaed;
  }
  * { margin: 0; padding: 0; box-sizing: border-box; }
  html, body {
    width: 1200px; height: 886px; overflow: hidden;
    background: var(--stage);
    font-family: "Roboto", Arial, sans-serif;
  }
  .canvas {
    width: 1200px; height: 886px;
    display: flex; flex-direction: column; align-items: center; justify-content: center;
    gap: 56px;
  }
  .card {
    width: 620px; height: 354px;
    border-radius: 22px;
    position: relative;
    box-shadow: 0 10px 28px rgba(20, 24, 36, 0.18);
  }
  .card-back { background: var(--dark-navy); display: flex; align-items: center; justify-content: center; }
  .card-front { background: var(--card-white); }

  .wordmark { display: flex; flex-direction: column; align-items: flex-start; }
  .wordmark-row { display: flex; align-items: center; gap: 12px; }
  .wordmark-name {
    font-weight: 500; letter-spacing: 0.12em; line-height: 1;
  }
  .wordmark-square { background: var(--brand-blue); }
  .wordmark-tagline {
    font-weight: 700; letter-spacing: 0.2em; text-transform: uppercase;
    margin-top: 8px;
  }
  .card-back .wordmark-name { color: #ffffff; font-size: 50px; }
  .card-back .wordmark-square { width: 16px; height: 16px; }
  .card-back .wordmark-tagline { color: #ffffff; font-size: 13px; }

  .card-front .wordmark { position: absolute; left: 44px; top: 118px; }
  .card-front .wordmark-name { color: var(--dark-navy); font-size: 34px; }
  .card-front .wordmark-square { width: 11px; height: 11px; }
  .card-front .wordmark-tagline { color: var(--dark-navy); font-size: 9px; margin-top: 6px; }

  .divider {
    position: absolute; left: 330px; top: 46px; width: 1px; height: 150px;
    background: var(--rule-grey);
  }
  .contact { position: absolute; left: 360px; top: 54px; }
  .contact-name {
    color: var(--accent-blue); font-weight: 500; font-size: 24px;
    text-transform: uppercase; letter-spacing: -0.01em; line-height: 1;
  }
  .contact-credentials {
    color: var(--accent-blue); font-size: 10.5px; margin-top: 4px; letter-spacing: 0.02em;
  }
  .contact-list { list-style: none; margin-top: 16px; }
  .contact-item {
    display: flex; align-items: center; gap: 10px;
    color: var(--text-grey); font-size: 14px; line-height: 1; margin-bottom: 10px;
  }
  .contact-icon { width: 14px; height: 14px; flex: none; }

  .offer {
    position: absolute; left: 0; right: 0; bottom: 66px; text-align: center;
    color: var(--accent-blue); font-weight: 700; font-size: 17px;
  }
  .services {
    position: absolute; left: 0; right: 0; bottom: 38px; text-align: center;
    color: var(--text-grey); font-size: 14px;
  }
  .services-sep { color: var(--brand-blue); margin: 0 4px; }
</style>
</head>
<body>
<main class="canvas">
  <section class="card card-back" aria-label="Card back">
    <div class="wordmark">
      <div class="wordmark-row">
        <span class="wordmark-name">VANTRELO</span>
        <span class="wordmark-square"></span>
      </div>
      <span class="wordmark-tagline">Nutrition - Fitness - Health</span>
    </div>
  </section>

  <section class="card card-front" aria-label="Card front">
    <div class="wordmark">
      <div class="wordmark-row">
        <span class="wordmark-name">VANTRELO</span>
        <span class="wordmark-square"></span>
      </div>
      <span class="wordmark-tagline">Nutrition - Fitness - Health</span>
    </div>

    <div class="divider"></div>

    <div class="contact">
      <h1 class="contact-name">Derek Fulham</h1>
      <p class="contact-credentials">MSc, CAT(C), RMT, CSCS, PN2</p>
      <ul class="contact-list">
        <li class="contact-item">
          <svg class="contact-icon" viewBox="0 0 14 14" aria-hidden="true">
            <rect x="0.5" y="2.5" width="13" height="9" rx="1.5" fill="var(--accent-blue)"/>
            <path d="M1.5 3.5 L7 8 L12.5 3.5" fill="none" stroke="#fff" stroke-width="1.2"/>
          </svg>
          derek@vantrelo.com
        </li>
        <li class="contact-item">
          <svg class="contact-icon" viewBox="0 0 14 14" aria-hidden="true">
            <circle cx="7" cy="7" r="6" fill="var(--accent-blue)"/>
            <ellipse cx="7" cy="7" rx="2.5" ry="6" fill="none" stroke="#fff" stroke-width="1"/>
            <line x1="1" y1="7" x2="13" y2="7" stroke="#fff" stroke-width="1"/>
          </svg>
          www.vantrelo.com
        </li>
        <li class="contact-item">
          <svg class="contact-icon" viewBox="0 0 14 14" aria-hidden="true">
            <circle cx="7" cy="7" r="6" fill="var(--accent-blue)"/>
          </svg>
          @derek_fulham
        </li>
      </ul>
    </div>

    <p class="offer">Contact us to receive a FREE assessment</p>
    <p class="services">
      Personal Training<span class="services-sep">|</span>Golf Fitness<span class="services-sep">|</span>Injury Rehab<span class="services-sep">|</span>Massage Therapy<span class="services-sep">|</span>Yoga
    </p>
  </section>
</main>
</body>
</html>
```